Business Card Design & Gift cards, Gift Cert, Donation Card

Retail Gift Store-in addition to Business Cards we'd like sequenced 2 sided Gift cards, Gift Certificate Cards, and Donation Cards.please see examples and email for clarificationlogos attached with examples-
Gift Card, Gift Certificate and Donation Card will all be same style just differant upper right title, with back side info as example.
business card, as example is single sided.
looking for additional ideas for layout

Industry/Entity Type

Business

Contact Information for Business Card

211 Newman St.East Tawas, MI 48730989.362.8730Office@BrewKrew.com

Requirements
Must have
• Blue as per example
• Logos provided
• like gradiant background

```html
<!DOCTYPE html>
<html lang="en">
<head>
<meta charset="utf-8">
<title>Tillow Marsh – Business Card &amp; Gift Card</title>
<link rel="stylesheet" href="https://fonts.googleapis.com/css2?family=Comic+Neue:wght@400;700&display=swap">
<style>
  :root {
    --page-bg: #4d4d4d;
    --card-bg: #ffffff;
    --ink: #111111;
    --ink-soft: #3a3a3a;
    --band-dark: #141414;
    --band-grey: #8a8a8a;
    --rule: #2a2a2a;
    --motif-blue: #c9d6f2;
    --motif-sun: #f6eaa6;
  }
  * { box-sizing: border-box; margin: 0; padding: 0; }
  html, body { width: 1105px; height: 1200px; overflow: hidden; }
  body {
    background: var(--page-bg);
    font-family: "Comic Neue", "Comic Sans MS", cursive;
    color: var(--ink-soft);
    position: relative;
  }
  .card {
    position: absolute;
    left: 192px;
    width: 720px;
    height: 412px;
    background: var(--card-bg);
    border-radius: 19px;
    overflow: hidden;
    box-shadow: 0 6px 14px rgba(0,0,0,0.45);
  }
  .card--business { top: 146px; }
  .card--gift { top: 602px; }

  /* Business card front */
  .contact { position: absolute; left: 50px; top: 56px; font-size: 22px; line-height: 28px; }
  .contact__address { margin-bottom: 10px; }
  .contact__row { display: flex; align-items: center; gap: 10px; line-height: 30px; }
  .contact__row svg { width: 17px; height: 17px; fill: var(--ink); flex: none; }
  .offerings { position: absolute; left: 50px; top: 228px; font-size: 22px; line-height: 30px; }
  .brand-name {
    position: absolute; right: 43px; top: 290px;
    font-size: 46px; font-weight: 400; color: var(--ink); letter-spacing: 1px;
  }
  .card-band { position: absolute; left: 0; bottom: 0; width: 720px; height: 22px; display: block; }

  /* Gift card back */
  .motif {
    position: absolute; left: 232px; top: 33px; width: 325px; height: 352px;
    background: linear-gradient(180deg, var(--motif-blue) 0%, var(--motif-blue) 65%, var(--motif-sun) 100%);
    opacity: 0.45; border-radius: 40px;
  }
  .card-number { position: absolute; right: 40px; top: 38px; font-size: 18px; color: var(--ink); }
  .field { position: absolute; left: 58px; display: flex; align-items: flex-end; color: var(--ink); }
  .field__label { white-space: nowrap; }
  .field__line { border-bottom: 1.5px solid var(--rule); margin-left: 12px; margin-bottom: 6px; }
  .field--major { font-size: 26px; font-weight: 700; }
  .field--minor { font-size: 21px; font-weight: 700; }
  .field--to { top: 82px; }
  .field--to .field__line { width: 542px; margin-left: 32px; }
  .field--from { top: 140px; }
  .field--from .field__line { width: 513px; }
  .field--issued { top: 222px; }
  .field--issued .field__line { width: 472px; margin-left: 6px; }
  .field--expiry { top: 270px; }
  .field--expiry .field__line { width: 442px; margin-left: 6px; }
  .field--employee { top: 318px; }
  .field--employee .field__line { width: 490px; margin-left: 20px; }
</style>
</head>
<body>
  <section class="card card--business">
    <div class="contact">
      <p class="contact__address">482 Larkfield Ave.<br>Harrow Bay, MI 48731</p>
      <p class="contact__row">
        <svg viewBox="0 0 24 24"><path d="M6.6 10.8a15.1 15.1 0 0 0 6.6 6.6l2.2-2.2c.3-.3.7-.4 1-.2 1.1.4 2.3.6 3.6.6.6 0 1 .4 1 1V20c0 .6-.4 1-1 1A17 17 0 0 1 3 4c0-.6.4-1 1-1h3.5c.6 0 1 .4 1 1 0 1.3.2 2.5.6 3.6.1.3 0 .7-.2 1z"/></svg>
        989.517.4296
      </p>
      <p class="contact__row">
        <svg viewBox="0 0 24 24"><path d="M2 5h20v14H2z M3.5 6.5 12 13l8.5-6.5" /><path d="M2 5h20L12 12.5z" fill="#fff"/></svg>
        Office@TillowMarsh.com
      </p>
      <p class="contact__row">
        <svg viewBox="0 0 24 24"><circle cx="12" cy="12" r="10"/><path d="M8 6c2 1 1 3 3 4s0 3 2 4-1 4-1 5M15 5c-1 2 2 3 4 3" stroke="#fff" stroke-width="1.6" fill="none"/></svg>
        www.TillowMarsh.com
      </p>
    </div>
    <div class="offerings">
      <p>Gourmet Food</p>
      <p>Fine Wines | Gift Baskets</p>
      <p>Kitchen &amp; Bath Accessories</p>
      <p>Candles | Cards | Soaps</p>
    </div>
    <p class="brand-name">TILLOW MARSH</p>
    <svg class="card-band" viewBox="0 0 720 22" preserveAspectRatio="none">
      <polygon points="0,0 471,0 464,22 0,22" fill="var(--band-dark)"/>
      <polygon points="477,0 720,0 720,22 470,22" fill="var(--band-grey)"/>
    </svg>
  </section>

  <section class="card card--gift">
    <div class="motif" role="img" aria-label="Faint decorative brand figure dancing in front of a rising sun"></div>
    <p class="card-number">Card Number : 58724</p>
    <div class="field field--major field--to"><span class="field__label">To :</span><span class="field__line"></span></div>
    <div class="field field--major field--from"><span class="field__label">Form :</span><span class="field__line"></span></div>
    <div class="field field--minor field--issued"><span class="field__label">Date&nbsp; Issued :</span><span class="field__line"></span></div>
    <div class="field field--minor field--expiry"><span class="field__label">Expiration Date :</span><span class="field__line"></span></div>
    <div class="field field--minor field--employee"><span class="field__label">Employee :</span><span class="field__line"></span></div>
  </section>
</body>
</html>
```